Talvoro bonds (Surety bond broker)

We are a broker of surety bonds, we need a presentation and a flyer with fresh design. Our core values are reliable, on time and customized service. We want to transmit to our clients, they can leave on us the process of underwriting and issuing a surety bond, so they can focus on their business with no distractions.

Font styles to use
Sans Serif
Other font styles liked:

Requirements
Must have
• Visually attractive.
Main Message: Fast service issuing and underwriting surety bonds, reliable, nos surprises, we are always one step ahead, customized and personalized bonding solutions.
Nice to have
• Have short version for the flyer, and extended version for the presentation.
Should not have
• We already have a logo (attached), maintain colors

```html
<!DOCTYPE html>
<html lang="es">
<head>
<meta charset="utf-8">
<title>Talvoro — Índice</title>
<link href="https://fonts.googleapis.com/css2?family=Aleo:wght@400;600&display=swap" rel="stylesheet">
<style>
  :root {
    --ink: #1f1e20;
    --brand-green: #6aa844;
    --leaf-light: #e6f1cf;
    --leaf-mid: #c3e09a;
    --leaf-deep: #9fd07a;
    --paper: #ffffff;
    --text: #1d1d1b;
  }
  html, body {
    margin: 0;
    padding: 0;
    width: 1200px;
    height: 848px;
    overflow: hidden;
    background: var(--paper);
  }
  .slide {
    position: relative;
    width: 1200px;
    height: 848px;
    overflow: hidden;
    font-family: "Aleo", Georgia, serif;
  }
  .backdrop {
    position: absolute;
    inset: 0;
    width: 1200px;
    height: 848px;
  }
  .slide-title {
    position: absolute;
    left: 106px;
    top: 366px;
    margin: 0;
    font-size: 88px;
    font-weight: 600;
    line-height: 1;
    color: var(--brand-green);
  }
  .contents {
    position: absolute;
    left: 673px;
    top: 178px;
    margin: 0;
    padding: 0;
    list-style: none;
  }
  .contents li {
    display: flex;
    align-items: baseline;
    height: 76.5px;
    font-size: 26px;
    color: var(--text);
  }
  .contents .num {
    color: var(--brand-green);
    width: 18px;
  }
  .contents .sep {
    color: var(--brand-green);
    margin: 0 10px 0 6px;
    font-weight: 400;
  }
  .brand {
    position: absolute;
    right: 32px;
    bottom: 36px;
    display: flex;
    align-items: center;
    gap: 10px;
    font-size: 36px;
    font-weight: 400;
    color: var(--brand-green);
    letter-spacing: 1px;
  }
  .brand-dot {
    width: 12px;
    height: 12px;
    border-radius: 50%;
    background: var(--brand-green);
  }
</style>
</head>
<body>
<main class="slide">
  <svg class="backdrop" viewBox="0 0 1200 848" aria-hidden="true">
    <defs>
      <linearGradient id="leafWash" x1="0.25" y1="1" x2="1" y2="0">
        <stop offset="0" stop-color="#ffffff"/>
        <stop offset="0.35" stop-color="#eef6dd"/>
        <stop offset="0.65" stop-color="#d7ebb1"/>
        <stop offset="1" stop-color="#a9d784"/>
      </linearGradient>
      <radialGradient id="glow" cx="0.3" cy="1" r="0.6">
        <stop offset="0" stop-color="#ffffff"/>
        <stop offset="1" stop-color="#ffffff" stop-opacity="0"/>
      </radialGradient>
    </defs>
    <rect class="wash" width="1200" height="848" fill="url(#leafWash)"/>
    <g class="facets" fill="#ffffff">
      <polygon points="760,20 1020,120 900,360 700,260" opacity="0.25"/>
      <polygon points="1010,0 1200,0 1200,250 1040,260" opacity="0.18"/>
      <polygon points="880,380 1180,300 1160,600 940,560" opacity="0.2"/>
      <polygon points="640,420 900,520 820,760 600,700" opacity="0.3"/>
      <polygon points="960,560 1200,520 1200,848 1000,848" opacity="0.22"/>
    </g>
    <rect class="glow" width="1200" height="848" fill="url(#glow)"/>
    <path class="shadow-band" d="M0,0 H649 C600,260 440,620 176,848 H0 Z" fill="var(--ink)"/>
    <path class="light-stripe" d="M540,0 C500,260 360,600 150,848" fill="none" stroke="#ffffff" stroke-width="8"/>
    <path class="light-stripe" d="M528,0 C490,260 350,600 140,848" fill="none" stroke="#eef5dc" stroke-width="2" opacity="0.6"/>
    <path class="green-stripe" d="M638,85 L614,260 C560,470 440,680 205,848 L245,848 C470,650 600,420 638,85 Z" fill="var(--brand-green)"/>
    <path class="green-stripe" d="M433,610 C380,700 300,790 195,848 L230,848 C320,780 390,700 433,610 Z" fill="var(--brand-green)"/>
  </svg>

  <h1 class="slide-title">Índice</h1>

  <ol class="contents">
    <li><span class="num">1</span><span class="sep">|</span>¿Quiénes somos?</li>
    <li><span class="num">2</span><span class="sep">|</span>Oferta de Valor</li>
    <li><span class="num">3</span><span class="sep">|</span>Nuestros Servicios</li>
    <li><span class="num">4</span><span class="sep">|</span>Productos</li>
    <li><span class="num">5</span><span class="sep">|</span>Ciclo de administración de Fianzas</li>
    <li><span class="num">6</span><span class="sep">|</span>Nuestros socios de negocio</li>
    <li><span class="num">7</span><span class="sep">|</span>Contacto</li>
  </ol>

  <div class="brand"><span class="brand-dot"></span>Talvoro</div>
</main>
</body>
</html>
```